BrivoNest Learning App for Children with Dyslexia

Project Description:

We are seeking a talented UI/UX designer to create engaging and intuitive designs for Brivonest, an innovative educational app designed to help children learn letters and words through a multisensory learning approach. The app aims to be particularly helpful for children with dyslexia, providing a supportive and interactive learning environment.

Key App Features & Design Requirements:

Account Creation Screen: Design a welcoming and straightforward sign-up page that allows users to register with their email or continue with Quarnix. The design should be clean, focusing on user-friendliness and accessibility, adhering to our terms of service and privacy policy.

Main Screen Design: The main screen should allocate at least 4/6 of its height to the interactive drawing area. It needs to display word prompts in both correct and scrambled orders and include options to "Show all Words," "Play all words," and a search function. The interface should be vibrant, engaging, and easy to navigate for children.

Profile Section: Create a user-friendly profile page that allows users to edit their profile image, name, username, email, links, and bio. The design should be clean and encourage user engagement.

BrivoTally Page: This section will display the user's learning progress, including rankings, a learning curve, and recently learned words. It should visually represent progress in a motivating and understandable way, suitable for a younger audience.

Visual and Auditory Feedback Implementation: Incorporate elements that support visual and auditory feedback, using dyslexia-friendly formats. This includes choosing appropriate colors, fonts, and auditory cues.

Accessibility and Customization Settings: Designs should include settings for adjusting visual contrast, font size, and the word list to accommodate individual preferences and needs.

Feel free to add more interactions and/or pages.

Design preferences:

Color Scheme: Use a bright, inviting color palette that stimulates learning and engagement without overwhelming the users.
Font Selection: Opt for fonts that are readable and accessible, particularly for users with dyslexia.
Icons and Graphics: Design custom icons and graphics that are cohesive with the app's theme and purpose. Illustrations should be simple, relatable, and supportive of the learning process.

Target Market(s)

Educational

Industry/Entity Type

Educational

Colors
0054AA
0677BA
7BADD7
CADEEF
E8F1F8
0094D4
00A9DD
6FCCEA
C7EBF8
E9F6FB

Requirements
Must have
• Educational app, a writing area, scoring and account management
Nice to have
• Statistics, Ranking Page, Settings and some nice visual features

```html
<!DOCTYPE html>
<html lang="en">
<head>
<meta charset="UTF-8">
<title>Brivonest – App Screens</title>
<link href="https://fonts.googleapis.com/css2?family=Jost:wght@400;500;600&display=swap" rel="stylesheet">
<style>
  :root{
    --navy:#0054AA;
    --ocean:#0677BA;
    --sky:#6FB9E8;
    --bg:#cfe2f1;
    --panel:#e8e8e8;
    --ink:#111;
    --grey-btn:#676767;
    --white:#fff;
    --chev:#777;
  }
  *{box-sizing:border-box;margin:0;padding:0}
  html,body{width:1200px;height:734px;overflow:hidden}
  body{background:var(--bg);font-family:"Jost",sans-serif;color:var(--ink);position:relative}
  .screen{position:absolute;top:72px;width:308px;height:598px;background:var(--white);border-radius:42px;overflow:hidden}
  .screen--signup{left:72px}
  .screen--main{left:447px}
  .screen--profile{left:821px}
  .abs{position:absolute}
  .status-time{top:19px;left:16px;font-size:14px}
  .status-icons{top:21px;right:16px}
  .home-bar{bottom:22px;left:100px;width:108px;height:4px;border-radius:2px;background:#111}
  .center{left:0;right:0;text-align:center}

  /* signup */
  .hero-art{left:55px;top:40px;width:198px;height:129px;border-radius:14px;background:linear-gradient(135deg,#7cc46a 0%,#f3e3c8 45%,#f4a259 75%,#6fb9e8 100%)}
  .brand-title{top:174px;font-size:29px;font-weight:500;color:var(--navy)}
  .brand-tag{top:207px;font-size:15px}
  .signup-title{top:246px;font-size:22px;font-weight:500;color:var(--navy)}
  .signup-sub{top:276px;font-size:13px;font-weight:500;letter-spacing:.2px}
  .email-input{left:15px;top:308px;width:281px;height:39px;border:1px solid var(--navy);border-radius:20px;font-size:12.5px;padding:0 16px;line-height:37px}
  .btn-primary{left:15px;top:361px;width:281px;height:39px;border-radius:20px;background:var(--navy);color:var(--white);font-size:15px;text-align:center;line-height:39px}
  .divider{top:421px;left:15px;width:281px;display:flex;align-items:center;gap:8px;font-size:14px}
  .divider span.line{flex:1;height:1px;background:var(--navy)}
  .btn-alt{left:15px;top:459px;width:281px;height:38px;border-radius:20px;background:var(--grey-btn);border:1px solid var(--navy);color:var(--white);font-size:15px;display:flex;align-items:center;justify-content:center;gap:8px}
  .btn-alt .dot{width:16px;height:16px;border-radius:50%;background:var(--white)}
  .terms{top:505px;font-size:14px;line-height:25px}

  /* main */
  .menu-icon{left:13px;top:54px}
  .points{top:47px;right:14px;font-size:14px;font-weight:500;letter-spacing:.3px}
  .draw-area{left:0;top:82px;width:308px;height:209px;background:var(--panel)}
  .pencil{left:118px;top:155px}
  .toggle{left:13px;top:304px;width:279px;height:54px;border-radius:27px;background:var(--ocean);display:flex}
  .toggle .seg{flex:1;display:flex;align-items:center;justify-content:center;font-size:14px;font-weight:500;color:var(--white)}
  .toggle .seg--active{background:var(--sky);border-radius:27px;font-weight:400}
  .word{height:36px;width:85px;border:1px solid var(--navy);border-radius:18px;font-size:14px;text-align:center;line-height:34px}
  .btn-results{left:50px;top:521px;width:203px;height:37px;border-radius:19px;background:var(--navy);color:var(--white);font-size:14px;font-weight:500;text-align:center;line-height:37px}

  /* profile */
  .back{left:20px;top:72px}
  .profile-title{top:53px;font-size:18px;font-weight:500}
  .avatar{left:119px;top:97px;width:68px;height:68px;border-radius:50%;background:linear-gradient(160deg,#9a9a9a,#d8d8d8)}
  .edit-image{top:172px;font-size:19px;font-weight:500;color:var(--ocean)}
  .row-label{left:13px;font-size:15px;font-weight:500}
  .row-value{left:116px;font-size:14px}
  .chev{left:282px}
</style>
</head>
<body>

<!-- Sign up -->
<section class="screen screen--signup">
  <div class="abs status-time">9:41</div>
  <svg class="abs status-icons" width="64" height="12" viewBox="0 0 64 12"><rect x="0" y="8" width="3" height="4" fill="#111"/><rect x="5" y="6" width="3" height="6" fill="#111"/><rect x="10" y="3" width="3" height="9" fill="#111"/><rect x="15" y="0" width="3" height="12" fill="#111"/><path d="M24 5a9 9 0 0 1 12 0M26.5 7.5a5 5 0 0 1 7 0" stroke="#111" stroke-width="1.8" fill="none"/><circle cx="30" cy="10.5" r="1.3" fill="#111"/><rect x="41" y="1" width="20" height="10" rx="2" stroke="#111" fill="none"/><rect x="43" y="3" width="16" height="6" fill="#111"/><rect x="62" y="4" width="2" height="4" fill="#111"/></svg>
  <div class="abs hero-art" role="img" aria-label="Illustration of children reading around a large open book"></div>
  <h1 class="abs center brand-title">Brivonest</h1>
  <p class="abs center brand-tag">Learn letters And Words</p>
  <h2 class="abs center signup-title">Create An Account</h2>
  <p class="abs center signup-sub">Enter Your Email To Sign Up For This App</p>
  <div class="abs email-input">email@inbox.test</div>
  <div class="abs btn-primary">Sign Up With Email</div>
  <div class="abs divider"><span class="line"></span><span>Or Continue With</span><span class="line"></span></div>
  <div class="abs btn-alt"><span class="dot"></span><span>Quarnix</span></div>
  <p class="abs center terms">By Clicking Continue,You Agree To Our<br>And Privacy Policy</p>
  <div class="abs home-bar"></div>
</section>

<!-- Main -->
<section class="screen screen--main">
  <div class="abs status-time">9:41</div>
  <svg class="abs status-icons" width="64" height="12" viewBox="0 0 64 12"><rect x="0" y="8" width="3" height="4" fill="#111"/><rect x="5" y="6" width="3" height="6" fill="#111"/><rect x="10" y="3" width="3" height="9" fill="#111"/><rect x="15" y="0" width="3" height="12" fill="#111"/><path d="M24 5a9 9 0 0 1 12 0M26.5 7.5a5 5 0 0 1 7 0" stroke="#111" stroke-width="1.8" fill="none"/><circle cx="30" cy="10.5" r="1.3" fill="#111"/><rect x="41" y="1" width="20" height="10" rx="2" stroke="#111" fill="none"/><rect x="43" y="3" width="16" height="6" fill="#111"/><rect x="62" y="4" width="2" height="4" fill="#111"/></svg>
  <svg class="abs menu-icon" width="18" height="14" viewBox="0 0 18 14"><path d="M0 1h18M0 7h18M0 13h18" stroke="#111" stroke-width="2"/></svg>
  <div class="abs points">16 Points</div>
  <div class="abs draw-area"></div>
  <svg class="abs pencil" width="70" height="60" viewBox="0 0 70 60"><path d="M28 33 L58 6 L64 12 L34 39 L26 42 Z M28 33 L34 39" stroke="#666" stroke-width="1.4" fill="none"/><path d="M26 42 C10 40 -2 44 6 48 C14 52 50 52 42 58 C38 60 20 58 16 56" stroke="#666" stroke-width="1.4" fill="none"/></svg>
  <div class="abs toggle"><div class="seg">Show All Words</div><div class="seg seg--active">Play All Words</div></div>
  <div class="abs word" style="left:13px;top:373px">Word 1</div>
  <div class="abs word" style="left:110px;top:373px">Word 2</div>
  <div class="abs word" style="left:206px;top:373px">Word 3</div>
  <div class="abs word" style="left:13px;top:419px">Word 4</div>
  <div class="abs word" style="left:110px;top:419px">···</div>
  <div class="abs btn-results">Show Me The Results</div>
  <div class="abs home-bar"></div>
</section>

<!-- Profile -->
<section class="screen screen--profile">
  <div class="abs status-time">9:41</div>
  <svg class="abs status-icons" width="64" height="12" viewBox="0 0 64 12"><rect x="0" y="8" width="3" height="4" fill="#111"/><rect x="5" y="6" width="3" height="6" fill="#111"/><rect x="10" y="3" width="3" height="9" fill="#111"/><rect x="15" y="0" width="3" height="12" fill="#111"/><path d="M24 5a9 9 0 0 1 12 0M26.5 7.5a5 5 0 0 1 7 0" stroke="#111" stroke-width="1.8" fill="none"/><circle cx="30" cy="10.5" r="1.3" fill="#111"/><rect x="41" y="1" width="20" height="10" rx="2" stroke="#111" fill="none"/><rect x="43" y="3" width="16" height="6" fill="#111"/><rect x="62" y="4" width="2" height="4" fill="#111"/></svg>
  <svg class="abs back" width="12" height="22" viewBox="0 0 12 22"><path d="M11 1 L1 11 L11 21" stroke="#111" stroke-width="1.6" fill="none"/></svg>
  <h2 class="abs center profile-title">Profile</h2>
  <div class="abs avatar" role="img" aria-label="User profile photo"></div>
  <div class="abs center edit-image">Edit Profile Image</div>

  <div class="abs row-label" style="top:218px">Name</div>
  <div class="abs row-value" style="top:219px">Mara Quill</div>
  <svg class="abs chev" style="top:222px" width="9" height="15" viewBox="0 0 9 15"><path d="M1 1l6.5 6.5L1 14" stroke="#777" stroke-width="1.4" fill="none"/></svg>

  <div class="abs row-label" style="top:256px">Username</div>
  <div class="abs row-value" style="top:257px">@username</div>
  <svg class="abs chev" style="top:260px" width="9" height="15" viewBox="0 0 9 15"><path d="M1 1l6.5 6.5L1 14" stroke="#777" stroke-width="1.4" fill="none"/></svg>

  <div class="abs row-label" style="top:293px">Email</div>
  <div class="abs row-value" style="top:294px">name@inbox.test</div>
  <svg class="abs chev" style="top:297px" width="9" height="15" viewBox="0 0 9 15"><path d="M1 1l6.5 6.5L1 14" stroke="#777" stroke-width="1.4" fill="none"/></svg>

  <div class="abs row-label" style="top:331px">Links</div>
  <div class="abs row-value" style="top:332px;line-height:24.5px">sitenook.test<br>mypage.test<br>yourpage.test</div>

  <div class="abs row-label" style="top:420px">Bio</div>
  <div class="abs row-value" style="top:421px">A description of this user</div>
  <svg class="abs chev" style="top:424px" width="9" height="15" viewBox="0 0 9 15"><path d="M1 1l6.5 6.5L1 14" stroke="#777" stroke-width="1.4" fill="none"/></svg>

  <div class="abs home-bar"></div>
</section>

</body>
</html>
```